stationary
envelopes, letterhead, biz card
I need single sided standard sized Business Card [3.5" x 2"]
doesnt matter whatever looks good
Professional
Morris Delvane
President
4612 Wintermoor Rd Ste 208-517
morris@vandrex.com
www.vandrex.com

```html
<!DOCTYPE html>
<html lang="en">
<head>
<meta charset="utf-8">
<title>Vandrex Business Card</title>
<link href="https://fonts.googleapis.com/css2?family=Questrial&display=swap" rel="stylesheet">
<style>
  :root {
    --backdrop: #2b2b2b;
    --card-light: #ffffff;
    --card-shade: #d9d9d9;
    --accent-blue: #2aa4dc;
    --band-black: #1c1c1c;
    --ink-dark: #2a2a2a;
    --ink-soft: #9a9a9a;
    --ink-white: #ffffff;
  }
  html, body {
    margin: 0;
    padding: 0;
    width: 1200px;
    height: 901px;
    overflow: hidden;
    background: var(--backdrop);
    font-family: "Questrial", "Century Gothic", sans-serif;
  }
  .business-card {
    position: absolute;
    left: 110px;
    top: 170px;
    width: 980px;
    height: 560px;
    border-radius: 22px;
    background: linear-gradient(135deg, var(--card-light) 0%, #f1f1f1 55%, var(--card-shade) 100%);
    overflow: hidden;
  }
  .brand {
    position: absolute;
    left: 80px;
    top: 110px;
    display: flex;
    align-items: center;
    gap: 22px;
  }
  .brand-square {
    width: 62px;
    height: 62px;
    background: var(--accent-blue);
  }
  .brand-name {
    font-size: 66px;
    color: var(--band-black);
    letter-spacing: 2px;
    line-height: 1;
  }
  .rule {
    position: absolute;
    left: 0;
    width: 100%;
    height: 4px;
    background: var(--accent-blue);
  }
  .rule-top { top: 262px; }
  .rule-bottom { top: 352px; }
  .name-band {
    position: absolute;
    left: 0;
    top: 272px;
    width: 100%;
    height: 74px;
    background: var(--band-black);
    display: flex;
    align-items: center;
    padding-left: 80px;
    box-sizing: border-box;
    font-size: 30px;
  }
  .person-name { color: var(--ink-white); font-weight: 700; }
  .divider { color: var(--ink-soft); margin: 0 22px; }
  .person-title { color: var(--ink-soft); }
  .contact {
    position: absolute;
    left: 80px;
    top: 392px;
    font-size: 24px;
    line-height: 34px;
    color: var(--ink-dark);
  }
  .contact p { margin: 0; }
  .contact .sep { margin: 0 14px; }
  .contact .web strong { font-weight: 700; }
</style>
</head>
<body>
  <div class="business-card">
    <div class="brand">
      <div class="brand-square"></div>
      <div class="brand-name">Vandrex</div>
    </div>
    <div class="rule rule-top"></div>
    <div class="name-band">
      <span class="person-name">Morris Delvane</span>
      <span class="divider">|</span>
      <span class="person-title">President</span>
    </div>
    <div class="rule rule-bottom"></div>
    <div class="contact">
      <p class="address">4612 Wintermoor Rd Ste 208-517</p>
      <p class="phones">P: 415.762.0193<span class="sep">|</span>F: 877.430.6158</p>
      <p class="email">E: morris@vandrex.com<span class="sep">|</span><span class="web">www.<strong>vandrex</strong>.com</span></p>
    </div>
  </div>
</body>
</html>
```